Website for a company offering full serivce charging solutions for electric cars

The company "tanu-werk" (english: "tanu-works") offering all-in-one-solutions for charging infrastructure for electric mobility.

There are four products:
1- Wallboxes for single-family homes
2- Solutions for property devloper/-management for property parking space
3- All-in-one-charging solution for municipalities/communities
4- Solutions for tourism/hotels/holiday appartments

The Website structure:
1. Main Page
2.1. Product Page Single Homes
2.2. Product Page Property Management / Parking
2.3. Product Page Municipality
2.4. Product Page Tourism
3. Contact Form / Request for information
4. Imprint / Legal

The Website should be built on Wordpress with a powerful possibility to simply add/modify specific landing pages.

We would like you to implement the website later and also maintain it if possible, but we would be able to do minor modifications by ourselfs (for A/B-Testing)

The website should be clear and simple, easy to understand.
Target group is mainly B2C without deeper knowledge of that topic.

It should suggest, that we will provide a very simple way to get the charging infrastructure done.

We need a contact form, maybe we will use Hubspot later.

Attached you will find a draft of the main page and a landing page (for 2.2) - it is just the content, please ignore the design. We would love to let you create a suitable design.
Also you will find some drafts a bit different for the same story.

I added also a few stock photos, but they don't need to be used! If you have better ideas, you are welcome!

Industry/Entity Type

Charging/Electric mobility

Number of Pages Required

2 page

Font styles to use
Sans Serif

Requirements
Must have
• Based on Wordpress, and the designer should be able to implement it on Wordpress on a later step

```html
<!DOCTYPE html>
<html lang="de">
<head>
<meta charset="utf-8">
<title>tanu-werk.de – Ladelösungen</title>
<link rel="stylesheet" href="https://fonts.googleapis.com/css2?family=Rubik:wght@400;500&family=Arimo:wght@400;700&display=swap">
<style>
:root{
  --bg-dark:#1d2431;
  --bg-header:#1a202c;
  --pink:#dd12a6;
  --purple:#7b5fc9;
  --purple-frame:#7a62cf;
  --text:#ffffff;
  --text-soft:#c9c6d8;
}
*{box-sizing:border-box;margin:0;padding:0}
html,body{width:1200px;height:2676px;overflow:hidden}
body{position:relative;background:var(--bg-dark);color:var(--text);font-family:"Arimo",Arial,sans-serif}
.site-header{position:absolute;left:0;top:0;width:1200px;height:112px;background:var(--bg-header)}
.brand{position:absolute;left:112px;top:34px;display:flex;align-items:center;gap:12px;font-family:"Rubik",sans-serif;font-weight:500;font-size:32px;color:#fff}
.brand-dot{width:14px;height:14px;border-radius:50%;background:var(--pink)}
.main-nav{position:absolute;right:111px;top:51px;display:flex;gap:48px;font-weight:700;font-size:13px}
.main-nav a{color:#fff;text-decoration:none}
.main-nav a.active{color:var(--pink)}
.hero{position:absolute;left:0;top:112px;width:1200px;height:530px;background:linear-gradient(100deg,#ee2bbd 0%,#d65cc7 40%,#a873de 70%,#9b7ee0 100%)}
.hero-title{position:absolute;left:108px;top:210px;font-family:"Rubik",sans-serif;font-weight:500;font-size:74px;color:#fff}
.partner-title{position:absolute;left:111px;top:748px;font-family:"Rubik",sans-serif;font-weight:500;font-size:36px;color:var(--pink)}
.partner-rule{position:absolute;left:111px;top:802px;width:50px;height:2px;background:var(--pink)}
.partner-text{position:absolute;left:113px;top:824px;width:431px;font-size:14px;line-height:26px;text-align:justify}
.partner-text p{margin-bottom:26px}
.frame-outline{position:absolute;left:572px;top:723px;width:101px;height:96px;border:3px solid var(--purple-frame)}
.frame-block{position:absolute;left:869px;top:905px;width:245px;height:277px;background:var(--pink)}
.partner-photo{position:absolute;left:588px;top:738px;width:502px;height:422px;background:linear-gradient(135deg,#e9b063 0%,#b98c62 35%,#5b5246 65%,#d8dde3 100%)}
.offer-card{position:absolute;top:1268px;width:311px;border:2px solid var(--purple);border-radius:10px;overflow:hidden}
.offer-card.pink{border-color:var(--pink)}
.card-head{height:76px;background:var(--purple);text-align:center;font-family:"Rubik",sans-serif;font-weight:500;font-size:24px;padding-top:20px}
.pink .card-head{background:var(--pink)}
.card-icon{position:relative;margin:-2px auto 0;width:132px;height:84px;border-radius:0 0 66px 66px;background:var(--purple);display:flex;align-items:center;justify-content:center}
.pink .card-icon{background:var(--pink)}
.card-list{list-style:none;padding:28px 2px 22px 22px;font-size:14px;line-height:26px}
.card-list li{position:relative;padding-left:27px;margin-bottom:11px}
.card-list li:last-child{margin-bottom:0}
.card-list li::before{content:"";position:absolute;left:2px;top:7px;width:10px;height:5px;border-left:2.5px solid var(--purple);border-bottom:2.5px solid var(--purple);transform:rotate(-45deg)}
.pink .card-list li::before{border-color:var(--pink)}
.sub-list{list-style:none;margin:10px 0 0 -24px;color:var(--text-soft);white-space:nowrap}
.sub-list li{padding-left:24px;margin:0}
.sub-list li::before{border:none!important;content:"›";transform:none;top:0;left:6px;width:auto;height:auto;color:#fff}
.site-footer{position:absolute;left:0;top:2352px;width:1200px;height:324px;background:var(--purple);text-align:center}
.footer-brand{margin-top:100px;font-family:"Rubik",sans-serif;font-weight:500;font-size:42px}
.footer-links{display:flex;justify-content:center;gap:43px;margin-top:20px;font-family:"Rubik",sans-serif;font-weight:500;font-size:15px}
.footer-links a{color:#fff;text-decoration:none}
.social{display:flex;justify-content:center;gap:7px;margin-top:26px}
.social span{width:33px;height:33px;border:1.5px solid #fff;border-radius:50%}
.copyright{margin-top:16px;font-family:"Rubik",sans-serif;font-size:14px}
</style>
</head>
<body>
<header class="site-header">
  <div class="brand"><span class="brand-dot"></span>tanu-werk.de</div>
  <nav class="main-nav">
    <a class="active" href="#">LÖSUNGEN</a><a href="#">UNTERNEHMEN</a><a href="#">SERVICES</a><a href="#">KARRIERE</a><a href="#">KONTAKT</a>
  </nav>
</header>

<section class="hero" role="img" aria-label="Ladestecker eines Elektroautos in pink-violettem Licht">
  <h1 class="hero-title">tanu-werk.de</h1>
</section>

<h2 class="partner-title">Tanu-werk ist Ihr Partner</h2>
<div class="partner-rule"></div>
<div class="partner-text">
  <p>wenn das Laden nicht nur einfach, sondern die Umsetzung auch aus einer Hand kommen soll</p>
  <p>Wir bieten Lösungen sowohl für Privatkunden, Geschäftskunden als auch Kommunen an, die schnell, fair und ohne Eigenleistung zu einer smarten Ladelösung für E-Fahrzeuge kommen möchten.</p>
  <p>Von der Beratung, über die Installation, Inbetriebnahme bis Abrechnung und Wartung bekommen Sie bei tanu-werk alles aus einer Hand. Auf Wunsch vermieten wir auch die Ladetechnik und übernehmen im gewerblichen Bereich die direkte Abrechnung mit dem Nutzer. Für Kommunen bieten wir den kostenfreien Full-Service an und beteiligen die Gemeinden an der Nutzung der Infrastruktur.</p>
</div>
<div class="frame-outline"></div>
<div class="frame-block"></div>
<div class="partner-photo" role="img" aria-label="Frau mit Smartphone lädt ihr weißes Elektroauto bei Sonnenuntergang"></div>

<article class="offer-card" style="left:111px">
  <div class="card-head">als Privatkunde</div>
  <div class="card-icon"><svg width="70" height="60" viewBox="0 0 70 60" fill="none" stroke="#fff" stroke-width="3"><circle cx="35" cy="12" r="7"/><path d="M23 36c0-8 5-13 12-13s12 5 12 13"/><path d="M6 20v22l14 14M64 20v22L50 56"/><path d="M14 30l8 10M56 30l-8 10"/></svg></div>
  <ul class="card-list">
    <li>Bestandsanalyse mit umfangreicher Beratung über die Möglichkeiten der Umsetzung</li>
    <li>Prüfung und Übernahme der Anmeldung verfügbarer Fördermöglichkeiten</li>
    <li>Auswahl an smarten Wallbox Lösungen, passend für Ihr Fahrzeug und Ihre Bedürfnisse</li>
    <li>Installation inkl. aller notwendigen Materialien Tätigkeiten (Durchbrüche, Erdarbeiten, etc.)</li>
    <li>Inbetriebnahme und Einweisung in die Ladetechnik</li>
    <li>Jährlich technische Wartung nach DGUV3</li>
    <li>Reparaturservice,unter Berücksichtigung der geltenden Garantie Ansprüche</li>
  </ul>
</article>

<article class="offer-card pink" style="left:445px">
  <div class="card-head">als Geschäftskunde</div>
  <div class="card-icon"><svg width="90" height="56" viewBox="0 0 90 56" fill="none" stroke="#fff" stroke-width="3"><circle cx="15" cy="12" r="8"/><circle cx="45" cy="12" r="8"/><circle cx="75" cy="12" r="8"/><path d="M3 48V36c0-8 24-8 24 0v12M33 48V36c0-8 24-8 24 0v12M63 48V36c0-8 24-8 24 0v12M3 40h84"/></svg></div>
  <ul class="card-list">
    <li>Durchführung einer individuellen Bedarfsanalyse inkl. Ermittlung der Anforderungen für:
      <ul class="sub-list">
        <li>Haus- und Immobilienverwaltungen</li>
        <li>Dienstleistungs- und Handelsunternehm</li>
        <li>Hotel und Beherbergungsbetriebe</li>
        <li>Parkraum- und Parkhausbetreiber</li>
        <li>Tourismus, Sport- und Freizeiteinrichtun</li>
      </ul>
    </li>
    <li>Planung und Projektierung des Installationsaufwands Materialverbrauch</li>
    <li>Leasing oder Kauf der Hardware</li>
    <li>Normgerechte Installation der Ladeinfrastruktur inkl. Durchbruch-, Brandschutz- und Erdarbeiten</li>
    <li>Bei Bestandsbauten Integration der Ladeinfrastruktur inGebäudesystemte chnik und Anpassung des etzanschlusses</li>
    <li>Inbetriebnahme der Anlage inkl. Prüf- und Messprotokollen</li>
    <li>Wiederkehrende technische Prüfung der Anlage nach DGUV 3</li>
    <li>Austausch und Reparatur Service</li>
    <li>Unterstützung bei der mtl. Nutzungsabr echnung und Einbindung in Ihre vorhan dene Abrechnungssysteme</li>
    <li>ODER direkte Abrechnung mit den Nutzern</li>
  </ul>
</article>

<article class="offer-card" style="left:778px">
  <div class="card-head">als Kommune</div>
  <div class="card-icon"><svg width="70" height="70" viewBox="0 0 70 70" fill="none" stroke="#fff" stroke-width="3"><path d="M25 14a10 10 0 0 1 20 0M20 14h30v12H20zM12 26h46v40H12zM4 66h62M29 66V52h12v14"/><path d="M19 34h6M32 34h6M45 34h6M19 43h6M32 43h6M45 43h6"/></svg></div>
  <ul class="card-list">
    <li>Konzeptionierung möglicher Ladeinfrastrukturen innerhalb Ihrer Gemeinde</li>
    <li>Planung und Projektsteuerung inkl. sämtlicher behördlicher Genehmigungsverfahren und Beantragung von Fördermitteln</li>
    <li>Fachgerechte Installation und Inbetriebnahme</li>
    <li>Regelmäßige Wartung gemäß Vorschrif</li>
    <li>Reparatur und Kundenservice</li>
    <li>Direkte Abrechnung mit dem Nutzer</li>
    <li>Beteiligung der Gemeinde am Umsatz</li>
    <li>Möglichkeit der Integration von Bonusprogrammen, mit denen der lokale Einzelhandel beworben wird</li>
  </ul>
</article>

<footer class="site-footer">
  <div class="footer-brand">tanu-werk.de</div>
  <nav class="footer-links">
    <a href="#">AGB</a><a href="#">Datenschutzerklarung</a><a href="#">Impressum</a><a href="#">Kontakt</a><a href="#">Karriere</a><a href="#">Faqs</a>
  </nav>
  <div class="social"><span></span><span></span><span></span><span></span><span></span></div>
  <p class="copyright">© Copyright 2022 Company Name.All Rights Reserved</p>
</footer>
</body>
</html>
```